Award-winnning Estate Agent needs a premium version of their 'For Sale' board design

We need a premium option for our 'For Sale' board design. We have a standard board that is attached to this brief, but were are looking to have a premium design version that we will use when selling exclusive properties. Our company name is Harbourline Vale Estates and the name for this is exclusive selection is: 'The Harbourline Collection'. The design needs to work with our current brand, but have a distinctive PREMIUM feel to it. I have uploaded the barnd guidelines and also some of the exisisting logo variations. We do NOT need a new logo but feel free to play around with colours, fonts, sizes etc. for the sign.

Target Market(s)

Property buyers & house hunters

Industry/Entity Type

Real Estate - Residential Property

Font styles to use
Sans Serif

Requirements
Must have
• A premium fee, must be square design, must be easy to read when driving past the sign
Nice to have
• I'm open ot ideas

```html
<!DOCTYPE html>
<html lang="en">
<head>
<meta charset="utf-8">
<title>The Harbourline Collection – For Sale Board</title>
<link href="https://fonts.googleapis.com/css2?family=Montserrat:wght@500;600;700&display=swap" rel="stylesheet">
<style>
  :root {
    --backdrop: #eceef1;
    --board-edge: #16171c;
    --brand-navy: #29307f;
    --brand-sky: #2e9bd6;
    --panel-white: #ffffff;
  }
  * { box-sizing: border-box; margin: 0; padding: 0; }
  html, body {
    width: 1200px;
    height: 735px;
    overflow: hidden;
    background: var(--backdrop);
  }
  .canvas {
    width: 1200px;
    height: 735px;
    display: flex;
    align-items: center;
    justify-content: center;
  }
  .sale-board {
    width: 680px;
    height: 680px;
    background: var(--brand-navy);
    border: 7px solid var(--board-edge);
    padding: 28px;
  }
  .board-panel {
    width: 100%;
    height: 100%;
    background: var(--panel-white);
    padding: 10px;
  }
  .panel-keyline {
    width: 100%;
    height: 100%;
    border: 2px solid var(--brand-sky);
    display: flex;
    flex-direction: column;
    align-items: center;
    justify-content: center;
    font-family: "Montserrat", sans-serif;
    color: var(--brand-navy);
    text-align: center;
  }
  .brand-mark {
    width: 58px;
    height: 58px;
    background: var(--brand-sky);
  }
  .collection-name {
    margin-top: 18px;
    font-size: 35px;
    font-weight: 600;
    letter-spacing: 0.2px;
    white-space: nowrap;
  }
  .sale-status {
    margin-top: 20px;
    font-size: 92px;
    font-weight: 700;
    line-height: 1;
    letter-spacing: 3px;
    white-space: nowrap;
  }
  .rule {
    width: 500px;
    height: 4px;
    background: var(--brand-sky);
    border: none;
  }
  .rule--upper { margin-top: 16px; }
  .rule--lower { margin-top: 14px; }
  .phone-number {
    margin-top: 14px;
    font-size: 74px;
    font-weight: 600;
    line-height: 1;
    letter-spacing: 2px;
    white-space: nowrap;
  }
  .web-address {
    margin-top: 20px;
    font-size: 25px;
    font-weight: 700;
    white-space: nowrap;
  }
</style>
</head>
<body>
  <main class="canvas">
    <section class="sale-board" aria-label="For Sale board">
      <div class="board-panel">
        <div class="panel-keyline">
          <div class="brand-mark" aria-hidden="true"></div>
          <p class="collection-name">The Harbourline Collection</p>
          <h1 class="sale-status">FOR SALE</h1>
          <hr class="rule rule--upper">
          <p class="phone-number">01632 960418</p>
          <hr class="rule rule--lower">
          <p class="web-address">www.harbourlinevaleestates.co.uk</p>
        </div>
      </div>
    </section>
  </main>
</body>
</html>
```